Carpentry framing business card and logo design

We need a logo that works well with baseball caps, tee shirts and sweat shirts. We are a carpentry framing company specializing in apartment complexes and large residential communities. We work in what is known as the tri state area southeastern Pennsylvania , New Jersey and northern Delaware . We would like to see die signs using the old English letter M and royal blue colors. Also we stress OSHA compliance and safety.

Industry/Entity Type

Residential

Contact Information for Business Card

Valdrick Construction Co Inc
4870 Quillford Lane
Brenmoor Vale 19087
Dale Valdrick
dale1valdrick@norvexmail.com
555-815-0926

```html
<!DOCTYPE html>
<html lang="en">
<head>
<meta charset="utf-8">
<title>Valdrick Construction Co Inc – Business Card</title>
<link href="https://fonts.googleapis.com/css2?family=Arimo:wght@400;700&display=swap" rel="stylesheet">
<style>
  :root{
    --backdrop:#ece9e4;
    --paper:#ffffff;
    --brand-red:#e2372d;
    --coral:#ef7a60;
    --royal:#3b3a9a;
    --shadow:rgba(40,30,20,.22);
  }
  *{margin:0;padding:0;box-sizing:border-box}
  html,body{width:1200px;height:818px;overflow:hidden}
  body{
    background:var(--backdrop);
    font-family:"Arimo",Arial,sans-serif;
    position:relative;
  }
  .card{
    position:absolute;
    top:250px;
    width:540px;
    height:309px;
    border-radius:4px;
    overflow:hidden;
    box-shadow:0 10px 28px var(--shadow);
  }
  .card--front{left:40px;background:var(--paper)}
  .card--back{left:620px;background:var(--brand-red)}
  .card__art{position:absolute;inset:0;width:100%;height:100%}

  .brand{
    position:absolute;left:42px;top:44px;
    display:flex;align-items:center;gap:14px;
  }
  .brand__square{
    width:34px;height:34px;background:var(--royal);flex:none;
  }
  .brand__name{
    color:var(--royal);
    font-weight:700;
    font-size:21px;
    letter-spacing:.04em;
    text-transform:uppercase;
    line-height:1.1;
  }
  .holder{
    position:absolute;left:42px;top:150px;
    color:var(--coral);
    font-size:24px;font-weight:400;
  }
  .contacts{
    position:absolute;left:42px;top:196px;
    list-style:none;
  }
  .contacts li{
    display:flex;align-items:center;gap:12px;
    color:var(--royal);
    font-size:16px;
    line-height:28px;
    white-space:nowrap;
  }
  .contacts svg{width:16px;height:16px;flex:none}
</style>
</head>
<body>

  <section class="card card--front" aria-label="Business card front">
    <svg class="card__art" viewBox="0 0 540 309" preserveAspectRatio="none" aria-hidden="true">
      <path d="M300 0 C470 10 548 120 540 309" fill="none" stroke="var(--royal)" stroke-width="3"/>
    </svg>

    <div class="brand">
      <span class="brand__square"></span>
      <span class="brand__name">Valdrick<br>Construction Co Inc</span>
    </div>

    <p class="holder">Dale Valdrick</p>

    <ul class="contacts">
      <li>
        <svg viewBox="0 0 16 16"><circle cx="8" cy="5" r="3.5" fill="var(--brand-red)"/><path d="M1.5 15.5c0-4 3-6 6.5-6s6.5 2 6.5 6z" fill="var(--brand-red)"/></svg>
        555-815-0926
      </li>
      <li>
        <svg viewBox="0 0 16 16"><rect x="1" y="3" width="14" height="10" fill="var(--brand-red)"/><path d="M1 3l7 6 7-6" fill="none" stroke="#fff" stroke-width="1.3"/></svg>
        dale1valdrick@norvexmail.com
      </li>
      <li>
        <svg viewBox="0 0 16 16"><path d="M8 1a5 5 0 0 0-5 5c0 4 5 9 5 9s5-5 5-9a5 5 0 0 0-5-5z" fill="var(--brand-red)"/><circle cx="8" cy="6" r="2" fill="#fff"/></svg>
        4870 Quillford Lane Brenmoor Vale 19087
      </li>
    </ul>
  </section>

  <section class="card card--back" aria-label="Business card back">
    <svg class="card__art" viewBox="0 0 540 309" aria-hidden="true">
      <ellipse cx="250" cy="330" rx="230" ry="300" fill="var(--paper)"/>
      <path d="M30 309 C30 80 140 22 260 22 C390 22 500 110 490 309" fill="none" stroke="var(--royal)" stroke-width="5"/>
    </svg>
  </section>

</body>
</html>
```